website design + images

We need a very appealing website design, layout and images for a sales analytics and sales productivity services company based in San Ramon, California. We need a good design for the home page and a template for all other pages (total 2 designs), and images for all inner pages (center column/banner images, and right hand top corner small images). There are about 18 inner pages.
Updates

Our existing website is www.brightvale.com
Our corporate colours are the ones that are there on the website. The logo is also shown. We will be changing the tagline to "accelerating revenue" or equivalent of that.

Please use the document "website for brightvale - template v2.doc" that I just uploaded for any reference to the content, navigation and wireframes. A few more clarifications are provided mainly for the link "Solutions".

Rajesh Kothuri

Hi,
We just uploaded ver 4 of the website template. There is more elaboration provided around the sublinks / sections for Solutions. Pls review and do get back if you need any clarifications.

Rgds
Rajesh Kothuri

Hi all,
We have so far received a few good designs. The designs are more or less on the right track. I would like to urge all of you to use the content and navigation provided in the document attached to our brief "website for brightvale - template v4.doc".  Please DO NOT use the content in our existing website www.brightvale.com . That is very old. We mentioned it only for reference to colour theme and broad details.

We have totally 13 sections in Solutions pages. They may be designed as a tree of links - first level sublinks - second level sublinks or links - first level sublinks and the remaining as sections within the first level sublinks pages. The page design would remain the same for all inner pages except careers. But after finalizing the design for the inner page, we will need images for the different inner pages.

Rgds
Rajesh Kothuri

Hi,
Thank you all for participation and very good designs. We are quite happy with what we have seen. We have now shortlisted about 4 vendors and sending invididual feedback to them for further improvement. We will be finalizing by Monday or Tuesday.  To the vendors who do not get feedback from us, thank you very much for participation. We may still do business in future for some of our other needs. 
The following are the process steps / expectations going forward, 
1. Feedback to the shortlisted designers and inviting improvements.
2. Review of the improved designs and further shortlist & feedback or direct finalization.
3. The design should be in 1024*768
2. Number of page designs = 2 (home page, inner page).
4. Home page design: instead of delivery model and customers, show one link "Why Us".
4. Solutions page design:  We will be needing an image in center column of solutions page that in a nutshell gives all the different types of solutions we provide. The entire set of solutions is in our attached document website for brightvale - template v4 and I am just uploading v5 with more description on sublinks.
5. After selection, we will be needing images for all the solution pages (total 12 pages under solutions + one solutions page), 1 image for Why Us?, 1 for Careers, and 3 for company (about us/ team, core values, ...) = total 18

Rgds
Rajesh Kothuri

Target Market(s)

We are a sales analytics and sales productivity services company. We help B2B companies with: sales planning; sales operations and sales measurement. The characteristics of our customers are:
- B2B medium enterprises (USD 100M- USD 2B in revenue) in the US
- Primary target verticals are: high-tech, engineering and professional services firms
- Our primary target customers titles are VP of Sales or VP of marketing; we could be selling to the CEO at companies with revenues below $200M

Industry/Entity Type

Consulting

Requirements
Must have
• - Clean, uncluttered design
• - Easy navigation; minimum clicks
Nice to have
• We have already built a content management system and wireframes for this site. To the extent possible, it would be great to leverage the wireframe structure we built, provided you don’t have to compromise on the look and feel and navigation of the site. Below is what we currently have as banner sizes and resolutions are:
• Home page banner size: 950 * 250’
• All pages – center top - image size: 558 * 160
• All pages – right hand top image – 175*135’

```html
<!DOCTYPE html>
<html lang="en">
<head>
<meta charset="utf-8">
<title>Brightvale – Customer Targeting</title>
<link rel="stylesheet" href="https://fonts.googleapis.com/css2?family=Noto+Sans:wght@400;700&family=Questrial&display=swap">
<style>
:root{
  --green:#2f9226;
  --green-dark:#1f7a18;
  --green-light:#44a83a;
  --blue:#3a6fc4;
  --blue-deep:#24489a;
  --blue-sky:#1f8fe8;
  --ink:#111;
  --panel:#f1f1f1;
  --frame:#3a3a3a;
  --white:#fff;
}
*{box-sizing:border-box;margin:0;padding:0}
html,body{width:1200px;height:898px;overflow:hidden}
body{position:relative;background:linear-gradient(#fff 0,#fff 640px,#ececec 824px);font-family:Verdana,"Noto Sans",sans-serif;color:var(--ink)}
.abs{position:absolute}

/* top bar */
.topbar{left:0;top:0;width:1200px;height:39px;background:linear-gradient(#3aa12f,var(--green-dark))}
.signin{left:700px;top:0;width:164px;height:43px;background:linear-gradient(#4a7fd6,var(--blue-deep));border-radius:0 0 8px 8px;color:#fff;font-weight:700;font-size:14px;display:flex;align-items:center;justify-content:center;gap:6px}
.util{top:0;height:39px;color:#fff;font-weight:700;font-size:14px;display:flex;align-items:center;gap:7px}
.util.contact{left:897px}
.util.sitemap{left:1034px}

/* brand */
.brand{left:73px;top:62px}
.brand-mark{width:68px;height:68px;border-radius:50%;background:var(--blue-deep)}
.brand-name{position:absolute;left:0;top:84px;font-family:Questrial,sans-serif;font-size:33px;color:var(--blue-deep);white-space:nowrap}
.brand-tag{position:absolute;left:0;top:122px;font-family:Questrial,sans-serif;font-size:19px;color:#333;white-space:nowrap}

/* main nav */
.mainnav{right:74px;top:72px;list-style:none;text-align:right}
.mainnav li{height:23.5px;font-family:"Noto Sans",sans-serif;font-weight:700;font-size:14px;line-height:19px;display:flex;justify-content:flex-end;align-items:center;gap:5px;white-space:nowrap}
.mainnav li::after{content:"";width:14px;height:14px;background:var(--blue)}
.mainnav li.active{color:#fff;font-weight:400}
.mainnav li.active::after{visibility:hidden}
.activebar{left:417px;top:97px;width:709px;height:16px;background:var(--blue)}

/* side menu */
.sidebox{left:73px;width:190px;background:var(--panel)}
.sidebox h3{background:linear-gradient(var(--green-light),var(--green-dark));color:#fff;font-size:13px;line-height:15px;padding:6px 7px;height:43px;letter-spacing:.2px}
.sidebox ul{list-style:none;padding:10px 6px}
.sidebox li{font-size:12.5px;line-height:21px;white-space:nowrap}
.sidebox li::before{content:"-";display:inline-block;width:17px}
.sidebox li.current{color:var(--blue-deep);font-weight:700}

/* banner */
.banner{left:268px;top:223px;width:660px;height:187px;background:var(--frame);box-shadow:0 3px 6px rgba(0,0,0,.4)}
.banner-copy{position:absolute;left:13px;top:7px;width:403px;height:172px;background:linear-gradient(120deg,var(--blue-sky),#1268d6);color:#fff;padding:20px 16px}
.banner-copy h2{font-family:Questrial,sans-serif;font-size:26px;font-weight:700;line-height:34px;white-space:nowrap}
.banner-copy p{font-family:"Noto Sans",sans-serif;font-size:13px;line-height:18px;margin-top:10px;font-weight:700}
.banner-photo{position:absolute;left:416px;top:7px;width:237px;height:172px;background:linear-gradient(135deg,#e2ddd4,#a7a39d 55%,#3c4150)}

/* article */
.article{left:277px;top:438px;width:645px}
.article h1{font-family:Questrial,sans-serif;font-weight:400;font-size:29px;color:var(--blue-deep);letter-spacing:.5px}
.article h1 span{color:var(--green)}
.article p{font-size:14px;line-height:17px;margin-top:16px}
.article h1 + p{margin-top:6px}

/* right column */
.aside-photo{left:935px;top:223px;width:194px;height:134px;border:3px solid var(--green);background:linear-gradient(135deg,#f3f3f3,#cfd6dc)}
.aside-panel{left:935px;top:357px;width:194px;height:381px;background:var(--panel);padding:8px 6px}
.aside-panel h3{font-family:"Noto Sans",sans-serif;color:var(--green);font-size:15px;line-height:19px;letter-spacing:.4px}
.aside-panel p{font-size:14px;line-height:17px;margin-top:2px}
.aside-panel p + p{margin-top:17px}
.readmore{left:935px;top:747px;width:194px;height:22px;background:linear-gradient(var(--green-light),var(--green-dark));color:#fff;font-weight:700;font-size:13px;line-height:22px;padding-left:6px;letter-spacing:.4px}

/* footer */
.footer{left:0;top:824px;width:1200px;height:74px;background:linear-gradient(var(--green-dark),#3aa22e 50%,var(--green-dark));color:#fff;text-align:center;font-weight:700;font-size:14px;line-height:19px;padding-top:16px;letter-spacing:.4px}
.footer .sep{margin:0 8px}
</style>
</head>
<body>
  <div class="abs topbar"></div>
  <div class="abs signin">
    <svg width="14" height="28" viewBox="0 0 14 28"><circle cx="7" cy="6" r="5" fill="#e8b93a"/><rect x="5.5" y="10" width="3" height="16" fill="#e8b93a"/><rect x="8" y="19" width="4" height="2" fill="#e8b93a"/><rect x="8" y="23" width="3" height="2" fill="#e8b93a"/></svg>
    Sign in/Register
  </div>
  <div class="abs util contact">
    <svg width="20" height="20" viewBox="0 0 20 20"><path d="M4 2l4 4-2 2c1 3 3 5 6 6l2-2 4 4-3 3C8 18 2 12 1 5z" fill="#7fd3f0"/></svg>
    Contact Us
  </div>
  <div class="abs util sitemap">
    <svg width="24" height="22" viewBox="0 0 24 22"><rect x="8" y="1" width="8" height="6" fill="#fff"/><rect x="1" y="15" width="6" height="6" fill="#fff"/><rect x="9" y="15" width="6" height="6" fill="#fff"/><rect x="17" y="15" width="6" height="6" fill="#fff"/><path d="M12 7v5M4 12h16M4 12v3M12 12v3M20 12v3" stroke="#fff" stroke-width="2" fill="none"/></svg>
    Sitemap
  </div>

  <div class="abs brand">
    <div class="brand-mark"></div>
    <div class="brand-name">Brightvale</div>
    <div class="brand-tag">Accelerating Revenue</div>
  </div>

  <div class="abs activebar"></div>
  <ul class="abs mainnav">
    <li>HOME</li>
    <li class="active">SOLUTIONS</li>
    <li>DELIVERY MODEL</li>
    <li>CUSTOMERS</li>
    <li>COMPANY</li>
    <li>CAREERS</li>
  </ul>

  <nav class="abs sidebox" style="top:223px;height:140px">
    <h3>Sales Planning<br>Analytics</h3>
    <ul>
      <li class="current">Customer Targeting</li>
      <li>Territory Planning</li>
      <li>Campaign Planning</li>
    </ul>
  </nav>
  <nav class="abs sidebox" style="top:374px;height:191px">
    <h3>Sales Productivity<br>Centers</h3>
    <ul>
      <li>Quoting center</li>
      <li>Proposal center</li>
      <li>CRM center</li>
      <li>Partner center</li>
      <li>Reference center</li>
      <li>Deal center</li>
    </ul>
  </nav>
  <nav class="abs sidebox" style="top:574px;height:194px">
    <h3>Sales Measurement<br>Analytics</h3>
    <ul>
      <li>Business Reporting</li>
      <li>Metrics &amp; Benchmarking</li>
      <li>Pipeline health check</li>
      <li>Sales rep scorecards</li>
      <li>What-if analyses</li>
      <li>Data services.</li>
    </ul>
  </nav>

  <section class="abs banner">
    <div class="banner-copy">
      <h2>SALES PLANNING ANALYTICS</h2>
      <p>It is a long established fact that a reader will be distracted by the readable content of a page when looking at its layout.</p>
    </div>
    <div class="banner-photo" role="img" aria-label="Photo of a business team meeting around a laptop"></div>
  </section>

  <article class="abs article">
    <h1>CUSTOMER <span>TARGETING</span></h1>
    <p>Lorem Ipsum is simply dummy text of the printing and typesetting industry. Lorem Ipsum has been the industry's standard dummy text ever since the 1500s, when an unknown printer took a galley of type and scrambled it to make a type specimen book. It has survived not only five centuries, but also the leap into electronic typesetting, remaining essentially unchanged.</p>
    <p>It was popularised in the 1960s with the release of Presstone sheets containing Lorem Ipsum passages, and more recently with desktop publishing software like Quillmark PageSetter including versions of Lorem Ipsum.</p>
    <p>It is a long established fact that a reader will be distracted by the readable content of a page when looking at its layout. The point of using Lorem Ipsum is that it has a more-or-less normal distribution of letters, as opposed to using 'Content here, content here', making it look like readable English.</p>
    <p>Many desktop publishing packages and web page editors now use Lorem Ipsum as their default model text, and a search for 'lorem ipsum' will uncover many web sites still in their infancy. Various versions have evolved over the years, sometimes by accident, sometimes on purpose (injected humour and the like).</p>
  </article>

  <div class="abs aside-photo" role="img" aria-label="Photo of hands reviewing printed sales charts"></div>
  <aside class="abs aside-panel">
    <h3>SALES MEASUREMENT ANALYTICS</h3>
    <p>Lorem Ipsum is simply dummy text of the printing and typesetting industry. Lorem Ipsum has been the industry's standard dummy text ever since the 1500s, when an unknown printer took a galley of type and scrambled it to make a type specimen book.</p>
    <p>It has survived not only five centuries, but also the leap into electronic typesetting, remaining essentially unchanged.</p>
  </aside>
  <div class="abs readmore">+Read More</div>

  <footer class="abs footer">
    Copyright © Brightvale 2010. All rights reserved.<br>
    disclaimer<span class="sep">|</span>contact us
  </footer>
</body>
</html>
```